Letterhead and matching envelope design for a dental office

We need a new stationary design, letterhead and envelope #10, for a dental office in Denver area. We are called Bright Harbor Dental. We want a simple and minimalistic design but not a boring design. I wish to have one good point that makes it look professional. I have attached our logo. Feel free to use either one. I want the design for letterhead and envelope look like a "matching pair" but not look the same. The envelope doesn't have to be white and it will have an address window on bottom left.

Target Market(s)

everyone who visits dentist (adults)

Industry/Entity Type

Dental

Font styles to use
Other font styles liked:
• close to font on logo or something that matches well

Requirements
Must have
• professional
• simple, minimalistic
• unique point that stands out
Nice to have
• matching but not same design for letterhead and envelope
Should not have
• not look like all the other boring designs
• no flowery, distracting feats

```html
<!DOCTYPE html>
<html lang="en">
<head>
<meta charset="utf-8">
<title>Bright Harbor Dental – Letterhead</title>
<link rel="stylesheet" href="https://fonts.googleapis.com/css2?family=Arimo:wght@400;700&family=Open+Sans:wght@400&display=swap">
<style>
  :root {
    --backdrop: #b9ddd2;
    --paper: #ffffff;
    --brand-green: #1f9a3a;
    --brand-green-soft: #dcefe0;
    --ink: #1c1c1c;
    --muted: #8a8a8a;
    --rule: #c9c9c9;
    --bar-gray: #9c9c9c;
    --photo-tone: #c9d3d8;
    --photo-warm: #d9b6a8;
  }
  * { box-sizing: border-box; margin: 0; padding: 0; }
  html, body { width: 1200px; height: 784px; overflow: hidden; }
  body { background: var(--backdrop); position: relative; font-family: "Arimo", Arial, sans-serif; }

  .letterhead {
    position: absolute; left: 330px; top: 10px;
    width: 540px; height: 764px;
    background: var(--paper);
    box-shadow: 0 6px 18px rgba(0,0,0,.12);
  }
  .corner-bar { position: absolute; left: 0; top: 0; width: 36px; height: 5px; background: var(--bar-gray); }

  .brand-mark {
    position: absolute; left: 18px; top: 54px;
    font-family: "Arimo", Arial, sans-serif; font-weight: 700;
    font-size: 14px; color: var(--brand-green);
    display: flex; align-items: center; gap: 8px;
  }
  .brand-mark .dot { width: 9px; height: 9px; border-radius: 50%; background: var(--brand-green); }

  .header-rule { position: absolute; left: 178px; right: 0; top: 150px; height: 5px; background: var(--brand-green); }

  .contact-block { position: absolute; left: 318px; top: 70px; width: 212px; }
  .contact-block .practice-name {
    font-family: "Arimo", Arial, sans-serif; font-weight: 700; font-size: 11px;
    color: var(--brand-green); margin-bottom: 6px;
  }
  .contact-block p { font-family: "Open Sans", Arial, sans-serif; font-size: 7px; line-height: 11px; color: var(--muted); display: flex; align-items: center; gap: 3px; white-space: nowrap; }
  .contact-block svg { width: 8px; height: 8px; flex: none; }

  .letter-body { position: absolute; left: 58px; top: 196px; width: 400px; color: var(--ink); font-size: 9px; line-height: 12.4px; }
  .letter-body p { margin-bottom: 12px; }

  .signature { position: absolute; left: 290px; top: 548px; width: 140px; height: 42px; background: linear-gradient(90deg, rgba(0,0,0,.04), rgba(0,0,0,.09)); border-radius: 3px; }

  .leaf-watermark { position: absolute; left: 160px; top: 560px; width: 180px; height: 80px; border-radius: 50%; background: radial-gradient(ellipse at center, var(--brand-green-soft), rgba(255,255,255,0) 70%); }

  .services-line { position: absolute; top: 640px; height: 1px; background: var(--rule); }
  .services-line.left { left: 90px; width: 122px; }
  .services-line.right { left: 290px; width: 140px; }
  .services-label {
    position: absolute; left: 212px; top: 630px; width: 78px; height: 21px;
    border: 1px solid var(--rule); background: var(--paper); font-size: 10px; font-weight: 700; color: var(--ink);
    display: flex; align-items: center; justify-content: center;
  }

  .service-photo { position: absolute; width: 44px; height: 40px; background: var(--photo-tone); clip-path: polygon(25% 0, 75% 0, 100% 50%, 75% 100%, 25% 100%, 0 50%); }
  .service-photo.a { left: 20px; top: 596px; }
  .service-photo.b { left: 58px; top: 620px; background: var(--photo-warm); }
  .service-photo.c { left: 426px; top: 620px; }
  .service-photo.d { left: 462px; top: 644px; }

  .services-list { position: absolute; left: 18px; right: 14px; font-family: "Open Sans", Arial, sans-serif; font-weight: 400; font-size: 9px; color: var(--muted); display: flex; gap: 14px; white-space: nowrap; }
  .services-list.row-one { top: 694px; padding-left: 30px; }
  .services-list.row-two { top: 714px; }
  .services-list li { list-style: none; display: flex; align-items: center; gap: 4px; }
  .services-list li::before { content: ""; width: 0; height: 0; border-left: 3.5px solid transparent; border-right: 3.5px solid transparent; border-bottom: 6px solid var(--brand-green); }

  .footer-band { position: absolute; left: 0; right: 0; bottom: 6px; height: 5px; background: var(--brand-green); }
</style>
</head>
<body>
  <main class="letterhead">
    <div class="corner-bar"></div>

    <div class="brand-mark"><span class="dot"></span>Bright Harbor Dental</div>

    <section class="contact-block">
      <div class="practice-name">Bright Harbor Dental</div>
      <p><svg viewBox="0 0 10 10"><circle cx="5" cy="5" r="4.2" fill="none" stroke="#8a8a8a"/><circle cx="5" cy="4.2" r="1.3" fill="#8a8a8a"/></svg>Suite 4, 2nd Floor, 18 Sample Rd, Harbor Point 0000</p>
      <p><svg viewBox="0 0 10 10"><circle cx="5" cy="5" r="4.2" fill="none" stroke="#8a8a8a"/><path d="M3.4 3h1l.5 1.2-.6.5a3 3 0 0 0 1.3 1.3l.5-.6 1.2.5v1a3.8 3.8 0 0 1-3.9-3.9z" fill="#8a8a8a"/></svg>00 9999 0000 &nbsp;<svg viewBox="0 0 10 10"><circle cx="5" cy="5" r="4.2" fill="none" stroke="#8a8a8a"/><rect x="3" y="3.5" width="4" height="3" fill="#8a8a8a"/></svg>00 9999 0000 &nbsp;<svg viewBox="0 0 10 10"><circle cx="5" cy="5" r="4.2" fill="none" stroke="#8a8a8a"/><rect x="3.4" y="2.6" width="3.2" height="4.8" rx=".6" fill="none" stroke="#8a8a8a"/></svg>0000 000 000</p>
      <p>All Appointments &amp; Correspondence to Harbor Point Rooms</p>
      <p>Provider No. 000000W &nbsp;|&nbsp; ABN 00 000 000 000</p>
    </section>

    <div class="header-rule"></div>

    <article class="letter-body">
      <p>Lorem Ipsum is simply dummy text of the printing and typesetting industry. Lorem Ipsum has been the industry's standard dummy text ever since the 1500s, when an unknown printer took a galley of type and scrambled it to make a type specimen book. It has survived not only five centuries, but also the leap into electronic typesetting, remaining essentially unchanged. It was popularised in the 1960s with the release of TypeSheet pages containing Lorem Ipsum passages, and more recently with desktop publishing software like PageSet Studio including versions of Lorem Ipsum.</p>
      <p>It is a long established fact that a reader will be distracted by the readable content of a page when looking at its layout. The point of using Lorem Ipsum is that it has a more-or-less normal distribution of letters, as opposed to using 'Content here, content here', making it look like readable English. Many desktop publishing packages and web page editors now use Lorem Ipsum as their default model text, and a search for 'lorem ipsum' will uncover many web sites still in their infancy. Various versions have evolved over the years, sometimes by accident, sometimes on purpose (injected humour and the like).</p>
      <p>Contrary to popular belief, Lorem Ipsum is not simply random text. It has roots in a piece of classical Latin literature from 45 BC, making it over 2000 years old. Elena Varga, a Latin professor at Northfield College in Westbrook, looked up one of the more obscure Latin words, consectetur, from a Lorem Ipsum passage, and going through the cites of the word in classical literature, discovered the undoubtable source. Lorem Ipsum comes from sections 1.10.32 and 1.10.33 of "de Finibus Bonorum et Malorum" structures, to generate Lorem Ipsum which looks reasonable. The generated Lorem Ipsum is therefore always free from repetition, injected humour, or non-characteristic words etc.</p>
    </article>

    <div class="leaf-watermark" role="img" aria-label="Faint green leaf decoration"></div>
    <div class="signature" role="img" aria-label="Handwritten signature of the sender"></div>

    <div class="service-photo a" role="img" aria-label="Photo of a dental implant model"></div>
    <div class="service-photo b" role="img" aria-label="Photo of a bright smile"></div>
    <div class="services-line left"></div>
    <div class="services-label">Services:</div>
    <div class="services-line right"></div>
    <div class="service-photo c" role="img" aria-label="Photo of a dental tool on a tooth"></div>
    <div class="service-photo d" role="img" aria-label="Photo of a tooth model"></div>

    <ul class="services-list row-one">
      <li>Bonding</li><li>Veneers</li><li>Dentures</li><li>Prosthodontics</li><li>Restoring Teeth</li><li>Teeth Whitening</li>
    </ul>
    <ul class="services-list row-two">
      <li>Cosmetic Dentistry</li><li>Root Canal Therapy</li><li>Routine Tooth Extractions</li><li>Cleanings &amp; Prevention, Exams</li>
    </ul>

    <div class="footer-band"></div>
  </main>
</body>
</html>
```